Basic / Quick Business Card

Quick easy design project!

Need a one sided basic business card that matches font & style of brand and bottle label for our gourmet condiment, Brindle Harrow Sauce. Brindle Harrow Sauce is sold in specialty retail, gourmet groceries and appears on chef-driven restaurant menus, so the target market is a high end, gourmet, artisan-made food-loving customer.

Files Included:
Sauce Bottle Label
Brindle Harrow Sauce Round Logos

**About the logos - the logo may be used in a circle or alone vertically as on side of the bottle label**

Layout of Card:
May be vertical or horizontal based on designer ideas.

Logo usage (in circle vs. stand alone vertical logo) is up to designers descretion as well.

Reverse side of business card will be various high end / professional product photos / food shots using us.kelbo.com system. **Designer on this project will NOT design a reserve for the card.**

Paper that will be used for printing:
Kelbo Standard - it's a WHITE paper, but we use a cream background on Brindle Harrow Sauce branding, so please take this into account on design to stay brand consistent.

Elements & Copy for Card:
1. Logo in either script horizontal or vertical version
2. Copy: "Artisan Made - Small Batch"
3. Name - Wes Dorrance
4. Title - Creator
5. Phone - xxx.xxx.xxxx
6. xxxx@brindleharrow.com
7. URL: brindleharrowsauce.com
8. Social Media: @getbrindleharrow on Quillo / Pagora / Lumigrid

Please provide final files in Illustrator or InDesign format.

```html
<!DOCTYPE html>
<html lang="en">
<head>
<meta charset="utf-8">
<title>Brindle Harrow Sauce — Business Card</title>
<link rel="stylesheet" href="https://fonts.googleapis.com/css2?family=Roboto+Slab:wght@300;400;700&display=swap">
<style>
  :root {
    --page-bg: #e6e2d8;
    --card-bg: #262424;
    --gold: #efa904;
    --cream: #f4f3e2;
    --ink: #262424;
    --text-light: #f1efe6;
  }
  html, body {
    margin: 0;
    padding: 0;
    width: 1200px;
    height: 1019px;
    overflow: hidden;
    background: var(--page-bg);
  }
  .stage {
    position: relative;
    width: 1200px;
    height: 1019px;
  }
  .card {
    position: absolute;
    left: 75px;
    top: 210px;
    width: 1050px;
    height: 600px;
    background: var(--card-bg);
    box-shadow: 0 10px 28px rgba(0,0,0,0.25);
    overflow: hidden;
    font-family: "Roboto Slab", Georgia, serif;
  }
  .card-art {
    position: absolute;
    inset: 0;
  }
  .brand-name {
    position: absolute;
    left: 95px;
    top: 88px;
    width: 270px;
    height: 270px;
    display: flex;
    align-items: center;
    justify-content: center;
    text-align: center;
    font-weight: 700;
    font-size: 38px;
    line-height: 1.08;
    color: var(--ink);
  }
  .tagline {
    position: absolute;
    left: 440px;
    top: 170px;
    font-weight: 300;
    font-size: 40px;
    line-height: 1.15;
    color: var(--ink);
  }
  .person {
    position: absolute;
    left: 160px;
    top: 420px;
  }
  .person-name {
    margin: 0;
    font-weight: 700;
    font-size: 34px;
    color: var(--gold);
  }
  .person-title {
    margin: 2px 0 0;
    font-weight: 300;
    font-size: 29px;
    color: var(--text-light);
  }
  .contact {
    position: absolute;
    left: 520px;
    top: 345px;
    margin: 0;
    padding: 0;
    list-style: none;
    font-weight: 300;
    font-size: 28px;
    line-height: 1.32;
    color: var(--text-light);
  }
  .contact .label,
  .contact .social { color: var(--gold); }
  .contact .sep { color: var(--text-light); }
</style>
</head>
<body>
<main class="stage">
  <article class="card">
    <svg class="card-art" width="1050" height="600" viewBox="0 0 1050 600" aria-hidden="true">
      <polygon class="band-edge" points="0,138 790,138 850,218 790,298 0,298" fill="var(--cream)"/>
      <polygon class="band" points="0,148 784,148 838,218 784,288 0,288" fill="var(--gold)"/>
      <circle class="badge" cx="230" cy="223" r="150" fill="var(--cream)" stroke="var(--ink)" stroke-width="10"/>
    </svg>

    <div class="brand-name">Brindle<br>Harrow<br>Sauce</div>

    <div class="tagline">Artisan Made<br>Small Batch</div>

    <div class="person">
      <p class="person-name">Wes Dorrance</p>
      <p class="person-title">Creator</p>
    </div>

    <ul class="contact">
      <li><span class="label">Phone</span> 555.0142.7788</li>
      <li>wes@brindleharrow.com</li>
      <li>brindleharrowsauce.com</li>
      <li class="social">Quillo <span class="sep">/</span> Pagora <span class="sep">/</span> Lumigrid</li>
      <li>@getbrindleharrow</li>
    </ul>
  </article>
</main>
</body>
</html>
```